Exciting opportunity to create logo and a label for our natural health brand.

About us

We are a customer centric health supplement brand who believes in natural medicine and high quality ingredients. We take a holistic approach to healthcare, with an eastern philosophy. We believe in being partners with our customers in their health care journey and are invested in their well being.

Our brand philosophy and values are attached (see Vorna philosophy.png). Our personality traits are:

- Natural
- Fresh
- Modern
- Balanced (in a holistic sense)

Task breakdown

1. Design a fresh feeling logo for us
- We want it to represent our values and high quality ingredients. We would like the quality of the product to be reflected in the branding and have a high end feel.
- Logo text must include Vorna Health Sciences
- We want the Vorna to be the focus of the logo (see uploaded image Vorna logo example.png)
The logo does not have to follow this layout, but we just want the Vorna to stand out. Feel free to use your creative license on this!

2. Create an attractive label to go on the supplement bottle
- The designs need to be eye catching, give a sense of high end ingredients and natural products and tie in with the logo to give a joined up feel.
- We are selling our products online and need them to really stand out from the competition.
- See examples of labels and packaging we like (1 -7 label design).

The initial label we would like you to design would be for our product Calm Drift. It is a product that assists in the management of Anxiety and stress. The label will appear on the bottle that holds the capsules for this supplement, see uploaded files (Example plain bottles.png). The bottles may be white as the picture shows or dark blue recyclable plastic or dark brown glass . We don't have the exact dimensions of the bottle yet, but I will follow up with these.

The label needs to include the following things:
1. The logo
2. The name of the product
3. The product is to help with the relief of Anxiety and Stress
4. Number of capsules the bottle contains
5. The back of the label should have
i) The ingredients
ii) Dosage
iii) Directions of use

Please use placeholder text where needed.

We look forward to seeing your design. Thank you.

```html
<!DOCTYPE html>
<html lang="en">
<head>
<meta charset="utf-8">
<title>Vorna Health Sciences – Calm Drift Label</title>
<link rel="stylesheet" href="https://fonts.googleapis.com/css2?family=Barlow:wght@500;600;700&display=swap">
<style>
  :root {
    --page-bg: #ffffff;
    --label-top: #2bb0f7;
    --label-bottom: #2a9fe2;
    --badge-blue: #2563b6;
    --badge-blue-dark: #2a66ad;
    --ring-grey: #a9abae;
    --ring-light: #d6d8da;
    --text-white: #ffffff;
    --foliage-tone: rgba(40, 110, 180, 0.28);
  }

  * { box-sizing: border-box; margin: 0; padding: 0; }

  html, body {
    width: 1200px;
    height: 750px;
    overflow: hidden;
    background: var(--page-bg);
    font-family: "Barlow", Arial, sans-serif;
  }

  .canvas {
    position: relative;
    width: 1200px;
    height: 750px;
  }

  .label {
    position: absolute;
    left: 360px;
    top: 25px;
    width: 480px;
    height: 700px;
    border-radius: 34px;
    background: linear-gradient(180deg, var(--label-top) 0%, var(--label-bottom) 100%);
    overflow: hidden;
    color: var(--text-white);
  }

  .foliage-area {
    position: absolute;
    right: 0;
    top: 60px;
    width: 150px;
    height: 560px;
    background: linear-gradient(90deg, rgba(40, 110, 180, 0) 0%, var(--foliage-tone) 70%, rgba(40, 110, 180, 0.12) 100%);
  }

  .brand {
    position: absolute;
    left: 0;
    right: 0;
    top: 92px;
    text-align: center;
    font-weight: 600;
    color: var(--text-white);
  }

  .brand-name {
    display: block;
    font-size: 124px;
    line-height: 1;
    letter-spacing: 2px;
  }

  .brand-descriptor {
    display: block;
    margin-top: 20px;
    font-size: 17px;
    letter-spacing: 15px;
    padding-left: 15px;
  }

  .product-badge {
    position: absolute;
    left: 100px;
    top: 295px;
    width: 280px;
    height: 280px;
    border-radius: 50%;
    background: linear-gradient(160deg, var(--ring-light), var(--ring-grey) 45%, var(--ring-light));
    padding: 12px;
  }

  .badge-core {
    width: 100%;
    height: 100%;
    border-radius: 50%;
    background: linear-gradient(90deg, var(--badge-blue), var(--badge-blue-dark));
    display: flex;
    flex-direction: column;
    align-items: center;
    justify-content: center;
    text-align: center;
  }

  .product-name {
    font-weight: 700;
    font-size: 40px;
    line-height: 1;
    letter-spacing: 0.5px;
  }

  .product-claim {
    margin-top: 14px;
    font-weight: 500;
    font-size: 17px;
    line-height: 1.2;
    letter-spacing: 1.6px;
  }

  .pack-info {
    position: absolute;
    left: 0;
    right: 0;
    top: 596px;
    text-align: center;
  }

  .capsule-count {
    font-weight: 600;
    font-size: 16px;
    letter-spacing: 1.5px;
  }

  .capsule-count strong {
    font-weight: 700;
    font-size: 20px;
    letter-spacing: 0.5px;
  }

  .pack-rule {
    width: 284px;
    height: 1px;
    margin: 8px auto 8px;
    background: var(--text-white);
    opacity: 0.85;
  }

  .supplement-type {
    font-weight: 500;
    font-size: 16px;
    letter-spacing: 1.8px;
  }
</style>
</head>
<body>
  <main class="canvas">
    <section class="label">
      <div class="foliage-area" role="img" aria-label="Faint botanical leaf illustration along the right edge"></div>

      <header class="brand">
        <span class="brand-name">Vorna</span>
        <span class="brand-descriptor">HEALTH SCIENCE</span>
      </header>

      <div class="product-badge">
        <div class="badge-core">
          <h1 class="product-name">Calm Drift</h1>
          <p class="product-claim">Reduce stress and<br>anxiety naturally</p>
        </div>
      </div>

      <footer class="pack-info">
        <p class="capsule-count"><strong>60</strong> Capsules</p>
        <div class="pack-rule"></div>
        <p class="supplement-type">Dietary Supplement</p>
      </footer>
    </section>
  </main>
</body>
</html>
```